Business Cards

Need business card design that I can update for new employees and details. Needs to incorporate our logo, be bright and fun (in line with tourism and holidays)
Would like a Map of Western Australia on the front with locations all the caravan parks we own (just purchased Tom Price so please include that as well as others listed on our website).
Target Market(s)
Famillies
Contact Information for Business Card
5 Cards -
Neil Perrow (Director) e: perrow@wattlebay.com.au p: 0491 570 156
Mira Perrow (Director) e: perrow@wattlebay.com.au p: 0491 570 157
Owen Halvey (General Manager) e: halvey@wattlebay.com.au p: 0491 570 158
Helen Halvey (General Manager) e: halvey@wattlebay.com.au p: 0491 570 159
Colin Danby (Training and Operations Manager) - e: danby@wattlebay.com.au p:0491 570 110
Colors
Look and feel

```html
<!DOCTYPE html>
<html lang="en">
<head>
<meta charset="utf-8">
<title>Wattle Bay Tourist Parks — Business Card</title>
<link href="https://fonts.googleapis.com/css2?family=Cinzel:wght@400;700&family=Roboto:wght@400&display=swap" rel="stylesheet">
<style>
  :root {
    --bg: #e4e5e6;
    --card-dark: #5a5b5d;
    --card-light: #f4f4f4;
    --teal: #3fb7c0;
    --teal-soft: #5fc3c9;
    --ink: #5c5d60;
    --white: #ffffff;
  }
  * { margin: 0; padding: 0; box-sizing: border-box; }
  html, body { width: 1200px; height: 886px; overflow: hidden; }
  body {
    background: var(--bg);
    display: flex;
    align-items: center;
    justify-content: center;
    gap: 48px;
    font-family: "Roboto", Arial, sans-serif;
  }
  .card {
    width: 520px;
    height: 298px;
    position: relative;
    overflow: hidden;
    box-shadow: 0 6px 18px rgba(0,0,0,0.18);
  }

  /* Back of card */
  .card-back {
    background: var(--card-dark);
    display: flex;
    flex-direction: column;
    align-items: center;
    justify-content: center;
  }
  .card-back .wordmark {
    display: flex;
    align-items: center;
    gap: 12px;
    color: var(--white);
  }
  .card-back .wordmark-square {
    width: 22px; height: 22px;
    background: var(--teal);
  }
  .card-back .wordmark-name {
    font-family: "Cinzel", Georgia, serif;
    font-weight: 400;
    font-size: 30px;
    letter-spacing: 3px;
    color: var(--white);
  }
  .card-back .website {
    position: absolute;
    bottom: 44px;
    left: 0; right: 0;
    text-align: center;
    color: var(--white);
    font-size: 12px;
    letter-spacing: 3px;
  }

  /* Front of card */
  .card-front {
    display: flex;
    background: var(--card-dark);
  }
  .brand-panel {
    width: 200px;
    background: var(--card-light);
    display: flex;
    flex-direction: column;
    align-items: center;
    justify-content: center;
    gap: 14px;
  }
  .brand-panel .wordmark-square {
    width: 34px; height: 34px;
    background: var(--teal);
  }
  .brand-panel .wordmark-name {
    font-family: "Cinzel", Georgia, serif;
    font-weight: 400;
    font-size: 21px;
    letter-spacing: 2px;
    color: var(--ink);
    text-align: center;
    line-height: 1.3;
  }
  .divider {
    width: 10px;
    display: flex;
    justify-content: space-between;
    background: var(--card-dark);
  }
  .divider span { width: 3px; background: var(--teal); }
  .divider span:first-child { background: var(--teal-soft); }
  .details {
    flex: 1;
    padding: 70px 0 0 34px;
    color: var(--white);
  }
  .person-name {
    font-family: "Cinzel", Georgia, serif;
    font-weight: 700;
    font-size: 21px;
    color: var(--teal);
    letter-spacing: 0.5px;
  }
  .person-role {
    font-family: "Cinzel", Georgia, serif;
    font-weight: 400;
    font-size: 14px;
    color: var(--teal);
    margin: 2px 0 0 14px;
  }
  .contact-list {
    list-style: none;
    margin-top: 30px;
    margin-left: 14px;
  }
  .contact-list li {
    display: flex;
    align-items: center;
    gap: 9px;
    font-size: 13px;
    line-height: 20px;
  }
  .contact-list svg { width: 12px; height: 12px; flex: none; }
</style>
</head>
<body>
  <section class="card card-back" aria-label="Business card back">
    <div class="wordmark">
      <div class="wordmark-square"></div>
      <div class="wordmark-name">Wattle Bay</div>
    </div>
    <p class="website">www.wattlebay.com.au</p>
  </section>

  <section class="card card-front" aria-label="Business card front">
    <div class="brand-panel">
      <div class="wordmark-square"></div>
      <div class="wordmark-name">Wattle Bay<br>Tourist Parks</div>
    </div>
    <div class="divider"><span></span><span></span></div>
    <div class="details">
      <h1 class="person-name">NEIL PERROW</h1>
      <p class="person-role">DIRECTOR</p>
      <ul class="contact-list">
        <li>
          <svg viewBox="0 0 12 12" aria-hidden="true"><path fill="#3fb7c0" d="M2.4 0.6l1.8 0 0.8 2.6-1.2 1a6.5 6.5 0 0 0 3 3l1-1.2 2.6 0.8 0 1.8c0 0.6-0.5 1-1 1A9.5 9.5 0 0 1 1.4 1.6c0-0.5 0.4-1 1-1z"/></svg>
          0491 570 156
        </li>
        <li>
          <svg viewBox="0 0 12 12" aria-hidden="true"><rect x="0.5" y="2" width="11" height="8" rx="1" fill="#3fb7c0"/><path d="M1 2.6l5 3.6 5-3.6" stroke="#5a5b5d" stroke-width="1" fill="none"/></svg>
          perrow@wattlebay.com.au
        </li>
        <li>
          <svg viewBox="0 0 12 12" aria-hidden="true"><circle cx="6" cy="6" r="5.5" fill="#3fb7c0"/><path d="M0.5 6h11M6 0.5c-2.5 3-2.5 8 0 11M6 0.5c2.5 3 2.5 8 0 11" stroke="#5a5b5d" stroke-width="0.8" fill="none"/></svg>
          www.wattlebay.com.au
        </li>
      </ul>
    </div>
  </section>
</body>
</html>
```